Dental office stationary (letterhead, envelopes), business cards, presentation folders

Nothing too dental outside of the logo. I will need all stationary, presentation folders, business cards. Would prefer to stay in the colors of the logo

Gordon Patel, DDS
Bright Haven Dental Implant Center
555-318-2790
info@brighthavendental.example
4817 NW Maple Crest Rd Unit B
Harbor Point, WA 00000

Also need appointment date and time
And cancellation policy
I want it to say “kindly ask for
A 48hr cancellation policy to avoid incurring a cancellation fee”

Industry/Entity Type

Dental

Colors
0054AA
0677BA
7BADD7
CADEEF
E8F1F8

Requirements
Must have
• Name of your office, name of doctor, address, phone number
Should not have
• Too much tooth/dental. Only the tooth in logo

```html
<!DOCTYPE html>
<html lang="en">
<head>
<meta charset="utf-8">
<title>Bright Haven Dental Implant Center – Stationery</title>
<link rel="stylesheet" href="https://fonts.googleapis.com/css2?family=Roboto:wght@400;500;700&display=swap">
<style>
  :root{
    --bg:#cbcbcb;
    --blue-light:#18bdee;
    --blue:#0e86cf;
    --blue-deep:#0a62b0;
    --teal:#1dbb9b;
    --ink:#333;
    --white:#fff;
  }
  *{box-sizing:border-box;margin:0;padding:0}
  html,body{width:1200px;height:1011px;overflow:hidden;background:var(--bg);font-family:'Roboto',sans-serif;color:var(--ink)}
  .canvas{position:relative;width:1200px;height:1011px}
  .piece{position:absolute;overflow:hidden;background:var(--white);box-shadow:0 2px 5px rgba(0,0,0,.25)}
  .piece svg.bg{position:absolute;left:0;top:0}
  .brand{font-family:'Roboto',sans-serif;font-weight:500;text-transform:uppercase;letter-spacing:.06em;text-align:center;line-height:1.2;color:var(--blue);white-space:nowrap}
  .brand.on-dark{color:var(--white)}
  .nowrap{white-space:nowrap}

  /* business card */
  .biz-card{left:53px;top:98px;width:325px;height:186px;border-radius:14px}
  .biz-card .info{position:absolute;left:16px;top:36px;color:var(--white);font-size:8.5px;line-height:1.3;white-space:nowrap}
  .biz-card .doctor{font-weight:700;font-size:10.5px;margin-bottom:26px}
  .biz-card .address{margin-bottom:20px}
  .contact-row{display:flex;align-items:center;gap:3px}
  .icon{width:7px;height:7px;flex:none}
  .biz-card .brand{position:absolute;left:210px;top:84px;width:100px;margin-left:-50px;width:200px;left:191px;font-size:9.5px;letter-spacing:.05em}

  /* appointment card */
  .appt-card{left:53px;top:315px;width:325px;height:185px;border-radius:14px}
  .appt-card .brand{position:absolute;left:0;top:24px;width:100%;font-size:14px}
  .appt-card .tab{position:absolute;left:0;top:67px;width:100%;text-align:center;color:var(--white);font-size:12px;line-height:14px}
  .appt-card .dash{position:absolute;left:21px;right:21px;top:109px;border-top:1px dashed #bbb}
  .appt-card .fields{position:absolute;left:21px;right:21px;top:127px;display:flex;font-size:9.5px;color:#444;align-items:flex-end}
  .field-line{border-bottom:1px solid #777;height:8px}
  .appt-card .policy{position:absolute;left:0;top:152px;width:100%;text-align:center;font-size:8.6px;line-height:1.3;color:#444}

  /* letterhead */
  .letterhead{left:402px;top:97px;width:286px;height:403px}
  .letterhead .brand{position:absolute;left:0;top:34px;width:100%;font-size:7.5px}
  .letterhead .body{position:absolute;left:26px;right:26px;top:124px;font-size:4.6px;line-height:1.3;color:#444}
  .letterhead .salute{font-size:6.5px;font-weight:500;margin-bottom:9px;color:#222}
  .letterhead .body p{margin-bottom:5px}
  .letterhead .closing{margin-top:10px;font-weight:500}
  .signature{width:40px;height:14px;margin-top:6px;background:linear-gradient(90deg,#e4e4e4,#f2f2f2)}
  .letterhead .foot{position:absolute;left:40px;right:40px;top:374px;text-align:center;font-size:4.8px;color:#444;white-space:nowrap}
  .letterhead .foot .rule{border-top:1px solid #888;margin:3px 10px}
  .letterhead .foot .row{display:flex;justify-content:center;gap:5px}

  /* envelope front */
  .envelope-front{left:715px;top:98px;width:431px;height:187px}
  .envelope-front .brand{position:absolute;left:0;top:52px;width:100%;font-size:13px}
  .envelope-front .address{position:absolute;left:0;top:169px;width:100%;text-align:center;font-size:7.3px;color:#444}

  /* envelope back */
  .envelope-back{left:713px;top:312px;width:435px;height:188px}
  .envelope-back .brand{position:absolute;left:0;top:16px;width:100%;font-size:11px}

  /* folder */
  .folder{top:590px;width:540px;height:360px;display:flex}
  .folder-outer{left:40px}
  .folder-inner{left:620px}
  .panel{position:relative;width:270px;height:360px;overflow:hidden}
  .panel-back{background:linear-gradient(160deg,var(--blue-light),var(--blue) 70%,#0b86b8)}
  .panel-front{background:linear-gradient(160deg,var(--blue),var(--blue-deep))}
  .panel-front .brand{position:absolute;left:0;top:160px;width:100%;font-size:16px}
  .panel-back .folder-contact{position:absolute;left:16px;right:16px;bottom:24px;color:var(--white);font-size:5.6px;text-align:center;white-space:nowrap}
  .folder-contact .rule{border-top:1px solid rgba(255,255,255,.7);margin:3px 0}
  .folder-contact .row{display:flex;justify-content:center;gap:6px}
  .panel-inside{background:linear-gradient(180deg,#f4f4f4,#e6e6e6)}
  .panel-inside + .panel-inside{border-left:1px solid #cfcfcf}
  .pocket{position:absolute;left:0;right:0;bottom:0;height:128px;background:linear-gradient(90deg,#1592c9,var(--blue-deep));border-top-right-radius:8px}
  .panel-inside + .panel-inside .pocket{border-top-right-radius:0;border-top-left-radius:8px}
</style>
</head>
<body>
<div class="canvas">

  <!-- Business card -->
  <section class="piece biz-card" aria-label="Business card">
    <svg class="bg" width="325" height="186" viewBox="0 0 325 186">
      <defs>
        <linearGradient id="gBiz" x1="0" y1="0" x2="1" y2="1">
          <stop offset="0" stop-color="#18bdee"/><stop offset="1" stop-color="#0a62b0"/>
        </linearGradient>
      </defs>
      <rect width="325" height="186" fill="url(#gBiz)"/>
      <circle cx="257" cy="93" r="106" fill="none" stroke="#1dbb9b" stroke-width="2"/>
      <circle cx="258" cy="93" r="104" fill="#fff"/>
      <rect x="258" y="0" width="67" height="186" fill="#fff"/>
    </svg>
    <div class="info">
      <div class="doctor">Gordon Patel, DDS</div>
      <div class="address">4817 NW Maple Crest Rd Unit B<br>Harbor Point, WA 00000</div>
      <div class="contact-row"><svg class="icon" viewBox="0 0 10 10"><path d="M2 1h2l1 2-1.3 1a6 6 0 0 0 2.3 2.3L7 5l2 1v2c0 .6-.4 1-1 1A8 8 0 0 1 1 2c0-.6.4-1 1-1z" fill="#fff"/></svg>555-318-2790</div>
      <div class="contact-row"><svg class="icon" viewBox="0 0 10 10"><rect x="0.5" y="2" width="9" height="6.5" fill="#fff"/><path d="M.5 2l4.5 3.5L9.5 2" fill="none" stroke="#0e86cf" stroke-width=".9"/></svg>info@brighthavendental.example</div>
      <div class="contact-row"><svg class="icon" viewBox="0 0 10 10"><circle cx="5" cy="5" r="4.5" fill="#fff"/><path d="M5 .5v9M.5 5h9M5 .5c-2.5 2.5-2.5 6.5 0 9M5 .5c2.5 2.5 2.5 6.5 0 9" fill="none" stroke="#0e86cf" stroke-width=".6"/></svg>www.brighthavendental.example</div>
    </div>
    <div class="brand">Bright Haven<br>Dental Implant Center</div>
  </section>

  <!-- Appointment card -->
  <section class="piece appt-card" aria-label="Appointment card">
    <svg class="bg" width="325" height="185" viewBox="0 0 325 185">
      <defs>
        <linearGradient id="gAppt" x1="0" y1="0" x2="1" y2="0">
          <stop offset="0" stop-color="#18bdee"/><stop offset="1" stop-color="#0a62b0"/>
        </linearGradient>
      </defs>
      <rect width="325" height="66" fill="url(#gAppt)"/>
      <rect y="68" width="325" height="3" fill="#1dbb9b"/>
      <path d="M83 68H242l-12 14H96z" fill="#1dbb9b"/>
    </svg>
    <div class="brand on-dark">Bright Haven<br>Dental Implant Center</div>
    <div class="tab">APPOINTMENT</div>
    <div class="dash"></div>
    <div class="fields">
      <span>DATE :&nbsp;</span><span class="field-line" style="flex:1.3"></span>
      <span>&nbsp;TIME :&nbsp;</span><span class="field-line" style="flex:1"></span>
    </div>
    <p class="policy">If you are unable to keep this appointment please notify us at least<br><b>48 hours</b> in advance to avoid a broken appointment charge</p>
  </section>

  <!-- Letterhead -->
  <section class="piece letterhead" aria-label="Letterhead">
    <svg class="bg" width="286" height="80" viewBox="0 0 286 80">
      <defs>
        <linearGradient id="gLetter" x1="0" y1="0" x2="1" y2="0">
          <stop offset="0" stop-color="#18bdee"/><stop offset="1" stop-color="#0a62b0"/>
        </linearGradient>
      </defs>
      <rect width="286" height="58" fill="url(#gLetter)"/>
      <path d="M0 58C60 -2 226 -2 286 58V80H0z" fill="#fff"/>
      <path d="M0 58C60 -2 226 -2 286 58" fill="none" stroke="#1dbb9b" stroke-width="1.5"/>
    </svg>
    <div class="brand">Bright Haven<br>Dental Implant Center</div>
    <div class="body">
      <div class="salute">Dear Mr. Alvarez,</div>
      <p>Thank you for choosing our practice for your implant care. This letter confirms the details of your upcoming visit and explains what to expect during your first consultation with our team.</p>
      <p>Please bring a list of current medications and any recent dental records. Our staff will review your history, take new images and discuss treatment options that suit your needs and schedule.</p>
      <p>We accept most insurance plans and offer flexible payment arrangements. If you have questions about coverage, our front desk will gladly help you before your visit so there are no surprises on the day.</p>
      <p>We look forward to meeting you and helping you enjoy a confident, healthy smile for years to come.</p>
      <div class="closing">Sincerely,</div>
      <div class="signature" role="img" aria-label="Handwritten signature"></div>
    </div>
    <div class="foot">
      <div>4817 NW Maple Crest Rd Unit B, Harbor Point, WA 00000</div>
      <div class="rule"></div>
      <div class="row"><span>555-318-2790</span><span>info@brighthavendental.example</span><span>www.brighthavendental.example</span></div>
    </div>
  </section>

  <!-- Envelope front -->
  <section class="piece envelope-front" aria-label="Envelope front">
    <svg class="bg" width="431" height="110" viewBox="0 0 431 110">
      <defs>
        <linearGradient id="gEnv" x1="0" y1="0" x2="1" y2="0">
          <stop offset="0" stop-color="#18bdee"/><stop offset="1" stop-color="#0a62b0"/>
        </linearGradient>
      </defs>
      <rect width="431" height="88" fill="url(#gEnv)"/>
      <path d="M0 88C90 -6 341 -6 431 88V110H0z" fill="#fff"/>
      <path d="M0 88C90 -6 341 -6 431 88" fill="none" stroke="#1dbb9b" stroke-width="2.2"/>
    </svg>
    <div class="brand">Bright Haven<br>Dental Implant Center</div>
    <div class="address">4817 NW Maple Crest Rd Unit B, Harbor Point, WA 00000</div>
  </section>

  <!-- Envelope back -->
  <section class="piece envelope-back" aria-label="Envelope back">
    <svg class="bg" width="435" height="60" viewBox="0 0 435 60">
      <defs>
        <linearGradient id="gFlap" x1="0" y1="0" x2="1" y2="0">
          <stop offset="0" stop-color="#18bdee"/><stop offset="1" stop-color="#0a62b0"/>
        </linearGradient>
      </defs>
      <path d="M0 0H435L427 36Q423 52 406 52H29Q12 52 8 36z" fill="url(#gFlap)"/>
    </svg>
    <div class="brand on-dark">Bright Haven<br>Dental Implant Center</div>
  </section>

  <!-- Presentation folder, outside -->
  <section class="piece folder folder-outer" aria-label="Presentation folder outside">
    <div class="panel panel-back">
      <div class="folder-contact">
        <div>4817 NW Maple Crest Rd Unit B, Harbor Point, WA 00000</div>
        <div class="rule"></div>
        <div class="row"><span>555-318-2790</span><span>info@brighthavendental.example</span><span>www.brighthavendental.example</span></div>
      </div>
    </div>
    <div class="panel panel-front">
      <div class="brand on-dark">Bright Haven<br>Dental Implant Center</div>
    </div>
  </section>

  <!-- Presentation folder, inside -->
  <section class="piece folder folder-inner" aria-label="Presentation folder inside">
    <div class="panel panel-inside"><div class="pocket"></div></div>
    <div class="panel panel-inside"><div class="pocket"></div></div>
  </section>

</div>
</body>
</html>
```